Business Card Design Project

We are a construction company in Orange County, CA. We need a two sided business card. We would like the back to be our logo with web URL. Front should included Name, title, address, phone, fax and email address.

our address is
627 West Dorrance Blvd, Suite 308
Harlow Bay, CA 92718

Our logo files are attached.

Construction

```html
<!DOCTYPE html>
<html lang="en">
<head>
<meta charset="utf-8">
<title>Braxel Business Card</title>
<link rel="stylesheet" href="https://fonts.googleapis.com/css2?family=Source+Sans+3:wght@400;600;700&display=swap">
<style>
  :root {
    --brand-navy: #1b4c7c;
    --ink-grey: #5a5a5a;
    --rule-grey: #c9c9c9;
    --card-white: #ffffff;
    --backdrop: #e7e4df;
  }
  * { margin: 0; padding: 0; box-sizing: border-box; }
  html, body {
    width: 1200px; height: 444px; overflow: hidden;
    background: var(--backdrop);
    font-family: "Source Sans 3", sans-serif;
  }
  .canvas { position: relative; width: 1200px; height: 444px; }
  .card {
    position: absolute; top: 76px;
    width: 514px; height: 293px;
    background: var(--card-white);
    border-radius: 14px;
  }
  .card-front { left: 68px; }
  .card-back { left: 617px; top: 74px; }

  .brand-name {
    position: absolute;
    color: var(--brand-navy);
    font-weight: 400;
    font-size: 40px;
    letter-spacing: 5px;
    line-height: 1;
    white-space: nowrap;
  }
  .card-front .brand-name { left: 48px; top: 130px; width: 226px; text-align: center; }

  .divider {
    position: absolute; left: 321px; top: 72px;
    width: 1px; height: 184px; background: var(--rule-grey);
  }
  .contact { position: absolute; left: 341px; top: 68px; color: var(--ink-grey); }
  .person-name { color: var(--brand-navy); font-weight: 700; font-size: 18px; line-height: 20px; }
  .person-title { font-size: 14px; line-height: 20px; margin-bottom: 10px; }
  .contact-list { list-style: none; font-size: 14px; }
  .contact-list li { display: flex; align-items: center; height: 18px; }
  .contact-list svg { width: 11px; height: 11px; margin-right: 8px; fill: var(--ink-grey); }
  .address { font-style: normal; font-size: 14px; line-height: 18px; margin-top: 14px; }

  .card-back .brand-name {
    left: 0; width: 100%; text-align: center; top: 112px;
  }
  .web-address {
    position: absolute; left: 0; width: 100%; top: 176px;
    text-align: center; color: var(--ink-grey);
    font-size: 12px; letter-spacing: 3px;
  }
</style>
</head>
<body>
<main class="canvas">
  <section class="card card-front" aria-label="Card front">
    <div class="brand-name">Braxel</div>
    <div class="divider"></div>
    <div class="contact">
      <div class="person-name">YOUR NAME</div>
      <div class="person-title">Title</div>
      <ul class="contact-list">
        <li><svg viewBox="0 0 12 12" aria-hidden="true"><path d="M2.5 1 4.5 1 5.2 3.6 4 4.5C4.6 6 6 7.4 7.5 8L8.4 6.8 11 7.5 11 9.5C11 10.3 10.3 11 9.5 11 5 11 1 7 1 2.5 1 1.7 1.7 1 2.5 1Z"/></svg>0246813579</li>
        <li><svg viewBox="0 0 12 12" aria-hidden="true"><path d="M1 4.5C1 3 3 2 6 2S11 3 11 4.5V5.5H8.5V4.3H3.5V5.5H1Z"/><rect x="2.5" y="6.5" width="7" height="4" rx="1"/></svg>0246813579</li>
        <li><svg viewBox="0 0 12 12" aria-hidden="true"><rect x="1" y="2.5" width="10" height="7" rx="0.8"/></svg>info@braxel.com</li>
        <li><svg viewBox="0 0 12 12" aria-hidden="true"><circle cx="6" cy="6" r="5"/></svg>www.braxel.com</li>
      </ul>
      <address class="address">
        627 West Dorrance Blvd<br>
        Suite 308<br>
        Harlow Bay, CA 92718
      </address>
    </div>
  </section>

  <section class="card card-back" aria-label="Card back">
    <div class="brand-name">Braxel</div>
    <div class="web-address">www.braxel.com</div>
  </section>
</main>
</body>
</html>
```